Plotvista Caribbean

We need a vibrant, user friendly and exciting website for our land search company called "plotVista" This application will help individuals locate and or list lots for sale within the Caribbean. We will offer a small cash back incentive to buyers that purchase land from our site, and we will charge a 1%-2% success fee to our sellers once a successful transaction is made. We would like to become a match making site, matching buyers and sellers on our platform. We will also include a service directory and marketing advertisement spot for other service providers for a fee. We would like to see a webdesign incorporating Caribbean colors (blue, green and yellow) with very modern clean lines, very picturesque and easy to use.

Industry/Entity Type

Real Estate

Coding

Coded - Design and coding required

Number of Pages Required

5+ page

Font styles to use
Sans Serif

Colors
ffffff
85acd3
b768aa
dbdbdb

Requirements
Nice to have
• Scenic photos of the ocean and beautiful landscape

```html
<!DOCTYPE html>
<html lang="en">
<head>
<meta charset="utf-8">
<title>plotVista – Search Land Near By You</title>
<link href="https://fonts.googleapis.com/css2?family=Montserrat:wght@400;500;600;700;800&family=Open+Sans:wght@400;600;700&display=swap" rel="stylesheet">
<style>
:root{
  --white:#ffffff;
  --blue:#85acd3;
  --blue-dark:#6f97c4;
  --purple:#b768aa;
  --grey:#dbdbdb;
  --grey-light:#f4f4f4;
  --card:#f5f5f5;
  --text:#555555;
  --dark:#222222;
  --line:#e2e2e2;
}
*{box-sizing:border-box;margin:0;padding:0}
html,body{width:1200px;height:2643px;overflow:hidden}
body{font-family:"Open Sans",Arial,sans-serif;color:var(--text);background:var(--white);font-size:13px;position:relative}
.container{position:absolute;left:76px;width:1048px}
h2.section-title{font-family:"Montserrat",Arial,sans-serif;font-weight:600;color:var(--purple);font-size:21px;letter-spacing:.3px}

/* header */
.site-header{height:72px;position:relative}
.brand{position:absolute;left:76px;top:18px;font-family:"Montserrat",sans-serif;font-weight:700;font-size:29px;color:#333}
.header-contact{position:absolute;right:76px;top:28px;display:flex;align-items:center;font-family:"Montserrat",sans-serif;font-size:12px}
.phone{display:flex;align-items:center;gap:10px;color:var(--blue);font-size:15px;font-weight:500;margin-right:42px}
.account a{color:#333;text-decoration:none;font-weight:500}
.account span{margin:0 14px;color:#999}
.main-nav{height:50px;background:var(--purple);display:flex;justify-content:space-between;align-items:center;padding:0 88px 0 102px}
.main-nav a{color:var(--white);font-family:"Montserrat",sans-serif;font-size:12.5px;font-weight:500;text-decoration:none}

/* hero */
.hero{position:absolute;top:122px;left:0;width:1200px;height:544px;background:linear-gradient(180deg,#2e3f5e 0%,#6b6f8a 18%,#e08a4a 32%,#5a6d86 42%,#8a8370 58%,#a8977d 78%,#8d7f6b 100%)}
.hero-arrow{position:absolute;top:246px}
.search-panel{position:absolute;left:300px;top:160px;width:600px;height:229px;background:rgba(40,40,40,.72);padding:18px 17px}
.search-panel h1{font-family:"Montserrat",sans-serif;font-weight:700;color:var(--white);text-align:center;font-size:28px;letter-spacing:.3px;margin-bottom:14px}
.field{background:var(--white);height:40px;border-radius:2px;font-size:11.5px;color:#666;display:flex;align-items:center;padding:0 12px;justify-content:space-between}
.field-row{display:flex;gap:10px;margin:10px 0}
.field-row .field{flex:1;height:36px}
.btn-search{height:40px;background:var(--purple);color:var(--white);font-family:"Montserrat",sans-serif;font-weight:600;font-size:14px;display:flex;align-items:center;justify-content:center;gap:8px;border-radius:2px}

/* welcome */
.welcome{top:719px}
.welcome-text{width:686px}
.welcome-text p{font-size:13.5px;line-height:26px;margin-top:18px}
.btn-grey{display:inline-flex;align-items:center;justify-content:center;width:164px;height:50px;background:var(--grey);color:#333;font-family:"Montserrat",sans-serif;font-weight:600;font-size:13px;margin-top:30px}
.cashback{position:absolute;left:717px;top:0;width:331px;height:252px;background:linear-gradient(160deg,#9ec0e2,#7ea5d0);color:var(--white);font-family:"Montserrat",sans-serif;font-weight:800;text-align:center;display:flex;flex-direction:column;justify-content:center;line-height:1.15}
.cashback .s{font-size:20px}.cashback .l{font-size:34px}.cashback .m{font-size:23px}
.divider{position:absolute;left:76px;top:1010px;width:1048px;height:1px;background:var(--line)}

/* listings */
.listings{top:1043px;width:690px}
.listing{height:188px;background:var(--card);margin-top:18px;position:relative}
.listings .section-title{margin-bottom:21px}
.listing-photo{position:absolute;left:23px;top:28px;width:204px;height:134px}
.listing-body{position:absolute;left:250px;top:22px;width:420px}
.listing-body h3{font-family:"Montserrat",sans-serif;font-weight:600;font-size:15px;color:var(--blue)}
.listing-body p{font-size:12.5px;line-height:21px;margin-top:4px}
.meta{font-size:12.5px;margin-top:4px}
.meta b{color:var(--purple);font-weight:600}
.meta i{font-style:normal;color:#aaa;margin:0 8px}
.price-row{display:flex;align-items:center;margin-top:12px}
.price{font-family:"Montserrat",sans-serif;font-weight:700;font-size:17px;color:var(--dark);width:134px}
.btn-details{background:var(--purple);color:var(--white);font-weight:600;font-size:13px;height:38px;width:118px;display:flex;align-items:center;justify-content:center}
.pager{display:flex;gap:5px;margin-top:32px}
.pager span{width:25px;height:25px;display:flex;align-items:center;justify-content:center;background:var(--grey);font-size:12px;color:#333}
.pager .arrow{background:var(--blue);color:var(--white)}
.pager .active{background:var(--purple);color:var(--white)}

/* news */
.news{position:absolute;left:793px;top:1043px;width:331px}
.news-item{height:141px;border-bottom:2px solid var(--line);position:relative;margin-top:0}
.news-list{margin-top:21px}
.news-photo{position:absolute;left:0;top:0;width:114px;height:95px}
.news-body{position:absolute;left:136px;top:-2px;width:195px}
.news-body .date{font-family:"Montserrat",sans-serif;color:var(--blue);font-weight:600;font-size:15px}
.news-body p{font-size:12.5px;line-height:21px;margin-top:6px}
.read{color:var(--purple);font-weight:600;font-size:12.5px;margin-top:5px;display:block}
.testimonial{position:absolute;left:793px;top:1510px;width:331px;height:245px;border:2px solid var(--line);padding:20px 24px}
.testimonial p{font-size:12.5px;line-height:24px;margin-top:14px}
.testimonial .who{color:var(--blue);font-weight:600;font-size:12.5px;margin-top:4px}
.dots{position:absolute;right:24px;bottom:20px;display:flex;gap:6px}
.dots i{width:9px;height:9px;border-radius:50%;background:#999}
.dots i:first-child{background:var(--purple)}

/* people */
.people{position:absolute;top:1806px;left:0;width:1200px;height:504px;background:var(--grey-light)}
.tabs{position:absolute;left:428px;top:49px;display:flex;gap:12px}
.tab{width:168px;height:53px;display:flex;align-items:center;justify-content:center;font-family:"Montserrat",sans-serif;font-weight:600;font-size:16px}
.tab.on{background:var(--white);color:var(--purple)}
.tab.off{background:var(--grey);color:#333;width:165px}
.people-panel{position:absolute;left:76px;top:102px;width:1048px;height:356px;background:var(--white)}
.p-arrow{position:absolute;top:165px}
.person{position:absolute;top:34px;width:194px;height:287px;border:1px solid #eee;text-align:center}
.person-photo{height:160px;background:linear-gradient(180deg,#e6e6e6,#bdbdbd)}
.person h4{font-family:"Montserrat",sans-serif;font-weight:600;color:var(--purple);font-size:13.5px;margin-top:18px}
.person p{font-size:13px;line-height:23px;margin-top:4px}
.person .read{color:var(--blue);margin-top:6px}

/* newsletter */
.newsletter{position:absolute;top:2310px;left:0;width:1200px;height:86px;background:var(--blue);display:flex;align-items:center;justify-content:center;gap:18px}
.newsletter h3{font-family:"Montserrat",sans-serif;color:var(--white);font-weight:600;font-size:22px}
.newsletter .input{width:270px;height:38px;background:var(--white);font-size:12.5px;color:#555;display:flex;align-items:center;padding:0 12px}
.newsletter .btn{width:134px;height:38px;background:var(--purple);color:var(--white);font-family:"Montserrat",sans-serif;font-weight:600;font-size:13px;display:flex;align-items:center;justify-content:center;margin-left:8px}

/* footer */
.site-footer{position:absolute;top:2396px;left:0;width:1200px;height:247px}
.f-col{position:absolute;top:42px}
.f-col h5{font-family:"Montserrat",sans-serif;color:var(--purple);font-weight:600;font-size:15px;margin-bottom:12px}
.f-col ul{list-style:none}
.f-col li{font-size:12.5px;line-height:27.5px;color:#333}
.f-col p{font-size:12.5px;line-height:21px;color:#333}
.f-input{width:267px;height:40px;border:1px solid #ccc;margin-top:14px;display:flex;align-items:center;justify-content:space-between;font-size:12px;color:#555;padding-left:14px}
.f-input span.send{width:45px;height:38px;background:var(--blue);display:flex;align-items:center;justify-content:center}
.social{display:flex;gap:12px;margin-top:4px}
.social i{width:18px;height:18px;border-radius:50%;background:#999}
.copy{font-size:11px;line-height:20px;color:#444;margin-top:52px}
</style>
</head>
<body>

<header class="site-header">
  <div class="brand">plotVista</div>
  <div class="header-contact">
    <div class="phone">
      <svg width="14" height="14" viewBox="0 0 24 24"><path fill="#333" d="M6.6 10.8a15.1 15.1 0 006.6 6.6l2.2-2.2a1 1 0 011-.25 11.4 11.4 0 003.6.6 1 1 0 011 1V20a1 1 0 01-1 1A17 17 0 013 4a1 1 0 011-1h3.5a1 1 0 011 1c0 1.25.2 2.45.57 3.57a1 1 0 01-.25 1z"/></svg>
      1-800-555-0142
    </div>
    <div class="account"><a href="#">SIGN IN</a><span>|</span><a href="#">LOG IN</a></div>
  </div>
</header>

<nav class="main-nav">
  <a href="#">HOME</a><a href="#">ABOUT US</a><a href="#">SERVICES</a><a href="#">SEARCH LAND</a><a href="#">BUYER</a><a href="#">SELLER</a><a href="#">BLOG</a><a href="#">CONTACT US</a>
</nav>

<section class="hero" role="img" aria-label="Sunset over a sandy beach path between wooden fences">
  <svg class="hero-arrow" style="left:72px" width="20" height="30" viewBox="0 0 20 30"><path d="M15 3 4 15l11 12" stroke="#fff" stroke-width="4" fill="none"/></svg>
  <svg class="hero-arrow" style="right:72px" width="20" height="30" viewBox="0 0 20 30"><path d="M5 3l11 12L5 27" stroke="#fff" stroke-width="4" fill="none"/></svg>
  <div class="search-panel">
    <h1>SEARCH LAND NEAR BY YOU</h1>
    <div class="field">Search Location, Area Land...</div>
    <div class="field-row">
      <div class="field">Select Land Sqft <svg width="9" height="6"><path d="M1 1l3.5 3.5L8 1" stroke="#666" fill="none"/></svg></div>
      <div class="field">Max Price <svg width="9" height="6"><path d="M1 1l3.5 3.5L8 1" stroke="#666" fill="none"/></svg></div>
      <div class="field">Min Price <svg width="9" height="6"><path d="M1 1l3.5 3.5L8 1" stroke="#666" fill="none"/></svg></div>
    </div>
    <div class="btn-search">
      <svg width="15" height="15" viewBox="0 0 16 16"><circle cx="6.5" cy="6.5" r="4.8" stroke="#fff" stroke-width="2.2" fill="none"/><path d="M10 10l4.5 4.5" stroke="#fff" stroke-width="2.4"/></svg>
      SEARCH
    </div>
  </div>
</section>

<section class="container welcome">
  <div class="welcome-text">
    <h2 class="section-title">WELCOME TO OUR WEBSITE</h2>
    <p>Aliquam molestie, mi et imperdiet euismod, dui purus auctor tellus, et interdum lacus lectus et ante. Sed accumsan sollicitudin sapien, sit amet adipiscing turpis gravida ac. In congue, neque ac lobortis volutpat, libero mauris varius mi, vitae suscipit ipsum ligula vitae risus. Duis aliquam nibh a dui iaculis viverra id a velit. Vivamus egestas risus in magna varius commodo. Sed semper viverra egestas. Etiam pretium porttitor lectus, vel ornare neque porta volutpat.</p>
    <a class="btn-grey">READ MORE</a>
  </div>
  <div class="cashback">
    <span class="s">GET</span>
    <span class="l">CASH BACK</span>
    <span class="m">INCENTIVE TO BUYERS<br>ON PURCHASE OF</span>
    <span class="l">LAND</span>
  </div>
</section>

<div class="divider"></div>

<section class="container listings">
  <h2 class="section-title">LAND FOR SALE</h2>
  <article class="listing">
    <div class="listing-photo" role="img" aria-label="Grassy coastline beside the sea" style="background:linear-gradient(180deg,#a9c6e0 0%,#d8e4ec 40%,#7f9d6a 60%,#4e6b32 100%)"></div>
    <div class="listing-body">
      <h3>LOREM IPSUM DOLOR SIT</h3>
      <p>Sed accumsan sollicitudin sapien, sit amet adipiscing turpis gravida ac egestas risus in magna..</p>
      <div class="meta"><b>Location:</b> 8901 Marmora Road<i>|</i><b>Area:</b> 2000Sft</div>
      <div class="price-row"><span class="price">$210, 22, 000</span><span class="btn-details">More Details</span></div>
    </div>
  </article>
  <article class="listing">
    <div class="listing-photo" role="img" aria-label="Field of purple flowers at sunset" style="background:linear-gradient(180deg,#e7a35a 0%,#c9874a 30%,#6b6a3f 50%,#7d69a8 75%,#5e4f8c 100%)"></div>
    <div class="listing-body">
      <h3>LOREM IPSUM DOLOR SIT</h3>
      <p>Sed accumsan sollicitudin sapien, sit amet adipiscing turpis gravida ac egestas risus in magna..</p>
      <div class="meta"><b>Location:</b> 8901 Marmora Road<i>|</i><b>Area:</b> 2000Sft</div>
      <div class="price-row"><span class="price">$210, 22, 000</span><span class="btn-details">More Details</span></div>
    </div>
  </article>
  <article class="listing">
    <div class="listing-photo" role="img" aria-label="Purple dusk over a bay and mountains" style="background:linear-gradient(180deg,#3a2f6e 0%,#b0508f 35%,#5a3f88 55%,#2d5f9e 80%,#1f3f78 100%)"></div>
    <div class="listing-body">
      <h3>LOREM IPSUM DOLOR SIT</h3>
      <p>Sed accumsan sollicitudin sapien, sit amet adipiscing turpis gravida ac egestas risus in magna..</p>
      <div class="meta"><b>Location:</b> 8901 Marmora Road<i>|</i><b>Area:</b> 2000Sft</div>
      <div class="price-row"><span class="price">$210, 22, 000</span><span class="btn-details">More Details</span></div>
    </div>
  </article>
  <div class="pager"><span class="arrow">«</span><span class="active">1</span><span>2</span><span>3</span><span>4</span><span class="arrow">»</span></div>
</section>

<aside class="news">
  <h2 class="section-title">LATEST NEWS</h2>
  <div class="news-list">
    <div class="news-item">
      <div class="news-photo" role="img" aria-label="Pier at sunset" style="background:linear-gradient(180deg,#5b4a8a,#d9765a 45%,#6b5a6e 70%,#3e3a4e)"></div>
      <div class="news-body"><div class="date">MAY 24, 2017</div><p>Sed accumsan sollicitudin sapien, sit amet...</p><span class="read">Read More</span></div>
    </div>
    <div class="news-item" style="margin-top:0">
      <div class="news-photo" role="img" aria-label="Beach path at sunset" style="background:linear-gradient(180deg,#4f6a8f,#e29a5a 35%,#8d8a76 60%,#a8977d)"></div>
      <div class="news-body"><div class="date">MAY 24, 2017</div><p>Sed accumsan sollicitudin sapien, sit amet...</p><span class="read">Read More</span></div>
    </div>
    <div class="news-item" style="border-bottom:none">
      <div class="news-photo" role="img" aria-label="Purple dusk over a bay" style="background:linear-gradient(180deg,#3a2f6e,#b0508f 40%,#2d5f9e 75%,#1f3f78)"></div>
      <div class="news-body"><div class="date">MAY 24, 2017</div><p>Sed accumsan sollicitudin sapien, sit amet...</p><span class="read">Read More</span></div>
    </div>
  </div>
</aside>

<aside class="testimonial">
  <h2 class="section-title">TESTIMONIALS</h2>
  <p>“ &nbsp;Aliquam molestie, mi et imperdiet euismod, dui purus auctor tellus, et interdum lacus lectus et ante accumsan sollicitudin sapien...”</p>
  <div class="who">-Name Heading</div>
  <div class="dots"><i></i><i></i><i></i><i></i></div>
</aside>

<section class="people">
  <div class="tabs"><div class="tab on">BUYERS</div><div class="tab off">SELLERS</div></div>
  <div class="people-panel">
    <svg class="p-arrow" style="left:18px" width="14" height="24" viewBox="0 0 14 24"><path d="M12 2 2 12l10 10" stroke="#999" stroke-width="2.5" fill="none"/></svg>
    <svg class="p-arrow" style="right:18px" width="14" height="24" viewBox="0 0 14 24"><path d="M2 2l10 10L2 22" stroke="#999" stroke-width="2.5" fill="none"/></svg>
    <div class="person" style="left:74px"><div class="person-photo" role="img" aria-label="Portrait of a buyer"></div><h4>NAME HEADING</h4><p>Vivamus egestas risus<br>in magna varius</p><span class="read">Read More</span></div>
    <div class="person" style="left:308px"><div class="person-photo" role="img" aria-label="Portrait of a buyer"></div><h4>NAME HEADING</h4><p>Vivamus egestas risus<br>in magna varius</p><span class="read">Read More</span></div>
    <div class="person" style="left:544px"><div class="person-photo" role="img" aria-label="Portrait of a buyer"></div><h4>NAME HEADING</h4><p>Vivamus egestas risus<br>in magna varius</p><span class="read">Read More</span></div>
    <div class="person" style="left:780px"><div class="person-photo" role="img" aria-label="Portrait of a buyer"></div><h4>NAME HEADING</h4><p>Vivamus egestas risus<br>in magna varius</p><span class="read">Read More</span></div>
  </div>
</section>

<section class="newsletter">
  <h3>NEWSLETTER SIGN UP</h3>
  <div class="input">Enter Email Address</div>
  <div class="btn">SIGN UP</div>
</section>

<footer class="site-footer">
  <div class="f-col" style="left:76px">
    <h5>SITE MAP</h5>
    <ul><li>Home</li><li>About Us</li><li>Services</li><li>Search Land</li><li>Buyer</li></ul>
  </div>
  <div class="f-col" style="left:216px;top:70px">
    <ul><li>Seller</li><li>Blog</li><li>Contact Us</li></ul>
  </div>
  <div class="f-col" style="left:368px">
    <h5>RESOURCES</h5>
    <ul><li>Duis aliquam</li><li>Nibh a dui iaculis</li><li>Viverra id a velit</li><li>Vivamus egestas</li></ul>
  </div>
  <div class="f-col" style="left:587px;width:280px">
    <h5>CONTACT INFO</h5>
    <p>Duis aliquam nibh a dui iaculis viverra id a velit egestas..</p>
    <div class="f-input">Enter Email Address<span class="send"><svg width="16" height="16" viewBox="0 0 16 16"><path d="M1 7.5 15 1l-4 14-3-5.5z" fill="#fff"/></svg></span></div>
  </div>
  <div class="f-col" style="left:901px">
    <h5>FOLLOW US</h5>
    <div class="social"><i></i><i></i><i></i><i></i><i></i><i></i></div>
    <div class="copy">Copyright© 2017. Company Name<br>All Right Reserved</div>
  </div>
</footer>

</body>
</html>
```